Market Research firm needs updated business cards with new logo

We need the logo to be included somewhere on the card (attached). We would also like the phrases "Independent, Objective, Comprehensive" and "Research You Can Trust" somewhere on the card. Front or back. Our colors are hex codes 6075a7, e48d25 and 5a5b5b. Though you are certainly not limited to those shades, whatever you produce should coordinate with them. I have also attached our favicon. Feel free to use it in your design, but please do not use it to replace the full logo.

Contact Information for Business Card

see project description

Font styles to use
Other font styles liked:
• Open Sans

Requirements
Must have
• the logo
• We use Open Sans font

```html
<!DOCTYPE html>
<html lang="en">
<head>
<meta charset="utf-8">
<title>Veridan Research — Business Card</title>
<link rel="stylesheet" href="https://fonts.googleapis.com/css2?family=Open+Sans:wght@400;600;700&display=swap">
<style>
  :root {
    --page-bg: #1b1b1b;
    --card-bg: #262626;
    --card-edge: #2e2e2e;
    --accent: #f5861f;
    --text-light: #f4f4f4;
    --text-soft: #e6e6e6;
  }
  * { box-sizing: border-box; margin: 0; padding: 0; }
  html, body {
    width: 1200px;
    height: 900px;
    overflow: hidden;
    background: var(--page-bg);
    font-family: "Open Sans", Arial, sans-serif;
  }
  .canvas {
    width: 1200px;
    height: 900px;
    display: flex;
    flex-direction: column;
    align-items: center;
    justify-content: center;
    gap: 36px;
  }
  .card {
    position: relative;
    width: 700px;
    height: 400px;
    background: linear-gradient(135deg, var(--card-bg) 0%, var(--card-edge) 100%);
    border-bottom: 6px solid var(--accent);
  }

  /* Brand name lockup */
  .brand {
    display: flex;
    align-items: center;
    gap: 12px;
    color: var(--text-light);
    font-weight: 600;
    white-space: nowrap;
  }
  .brand-dot {
    border-radius: 50%;
    background: var(--accent);
    flex: none;
  }

  /* Front */
  .card-front .brand {
    position: absolute;
    top: 130px;
    left: 0;
    right: 0;
    justify-content: center;
    font-size: 52px;
    letter-spacing: 0.5px;
  }
  .card-front .brand-dot { width: 30px; height: 30px; }
  .tagline {
    position: absolute;
    bottom: 34px;
    left: 0;
    right: 0;
    text-align: center;
    color: var(--text-soft);
    font-size: 17px;
    line-height: 1.45;
    letter-spacing: 1.2px;
  }

  /* Back */
  .card-back .brand {
    position: absolute;
    top: 160px;
    left: 40px;
    width: 310px;
    font-size: 30px;
  }
  .card-back .brand-dot { width: 18px; height: 18px; }
  .divider {
    position: absolute;
    left: 380px;
    top: 110px;
    width: 2px;
    height: 190px;
    background: var(--accent);
  }
  .contact {
    position: absolute;
    left: 410px;
    top: 108px;
    color: var(--text-soft);
  }
  .contact-name {
    color: var(--accent);
    font-weight: 600;
    font-size: 27px;
    letter-spacing: 1.5px;
    text-transform: uppercase;
    line-height: 1.1;
  }
  .contact-title {
    font-size: 18px;
    letter-spacing: 1px;
    margin-bottom: 18px;
  }
  .contact-address {
    font-size: 17px;
    letter-spacing: 1px;
    line-height: 1.4;
    font-style: normal;
    margin-bottom: 10px;
  }
  .contact-list { list-style: none; }
  .contact-item {
    display: flex;
    align-items: center;
    gap: 10px;
    font-size: 17px;
    letter-spacing: 0.8px;
    line-height: 1.55;
  }
  .contact-icon { width: 13px; height: 13px; flex: none; }
</style>
</head>
<body>
<main class="canvas">

  <section class="card card-front" aria-label="Card front">
    <div class="brand">
      <span class="brand-dot"></span>
      <span class="brand-name">Veridan Research</span>
    </div>
    <p class="tagline">
      Independent - Objective - Comprehensive<br>
      Research You Can Trust
    </p>
  </section>

  <section class="card card-back" aria-label="Card back">
    <div class="brand">
      <span class="brand-dot"></span>
      <span class="brand-name">Veridan Research</span>
    </div>
    <div class="divider"></div>
    <div class="contact">
      <h1 class="contact-name">Daniel Hart</h1>
      <p class="contact-title">Director</p>
      <address class="contact-address">
        27 Alder Lane<br>
        Brookfield, VA 22010
      </address>
      <ul class="contact-list">
        <li class="contact-item">
          <svg class="contact-icon" viewBox="0 0 16 16" aria-hidden="true">
            <path d="M4 1 L6.5 1 L7.5 5 L5.5 6.2 C6.4 8.2 7.8 9.6 9.8 10.5 L11 8.5 L15 9.5 L15 12 C15 13.7 13.7 15 12 15 C6 15 1 10 1 4 C1 2.3 2.3 1 4 1 Z" fill="none" stroke="var(--accent)" stroke-width="1.5"/>
          </svg>
          <span>555 201-4830</span>
        </li>
        <li class="contact-item">
          <svg class="contact-icon" viewBox="0 0 16 16" aria-hidden="true">
            <rect x="1" y="3" width="14" height="10" fill="none" stroke="var(--accent)" stroke-width="1.5"/>
            <path d="M1 3 L8 9 L15 3" fill="none" stroke="var(--accent)" stroke-width="1.5"/>
          </svg>
          <span>info@veridanresearch.com</span>
        </li>
        <li class="contact-item">
          <svg class="contact-icon" viewBox="0 0 16 16" aria-hidden="true">
            <circle cx="8" cy="8" r="7" fill="none" stroke="var(--accent)" stroke-width="1.4"/>
            <ellipse cx="8" cy="8" rx="3" ry="7" fill="none" stroke="var(--accent)" stroke-width="1.2"/>
            <path d="M1 8 H15 M2.5 4.5 H13.5 M2.5 11.5 H13.5" stroke="var(--accent)" stroke-width="1.2"/>
          </svg>
          <span>www.veridanresearch.com</span>
        </li>
      </ul>
    </div>
  </section>

</main>
</body>
</html>
```